Web Design

We need a website for a company based in Doha Qatar called
Lumara Maid Service.

It is the number one maid cleaning service company, and we have branches all over qatar.

Luxury Cleaning Service Provider.

The color scheme is gold, yellow and black like the logo.

Before they get to the website, there is an intro video.

The website should depict luxury.

Target Market(s)

People who need maids at their houses.

Industry/Entity Type

Cleaning Service

Requirements
Must have
• Luxury, Sleek, Modern

The opening sequence is a video which I already have. Its too big to upload here so I am going to put it on youtube.

After the opening sequence, the home page should have a widescreen photo background and it should change every five seconds, the first background photo should be of qatar westbay skyline. Then the second background should be of maid photos in cleaning positions. Then the third background should be of cleaner photos etc.

We will send you all the tabs and all the content later.

```html
<!DOCTYPE html>
<html lang="en">
<head>
<meta charset="UTF-8">
<title>Lumara Maid Service</title>
<link rel="stylesheet" href="https://fonts.googleapis.com/css2?family=Montserrat:wght@400;600;700&display=swap">
<style>
  :root {
    --sky-top: #1d2a33;
    --sky-mid: #4a5458;
    --sky-glow: #9a9482;
    --city-low: #262c30;
    --gold: #e0a826;
    --gold-light: #f3c544;
    --panel-top: #2a170b;
    --panel-bottom: #050302;
    --photo-light: #e9e4dc;
    --photo-mid: #d3cbc0;
    --photo-dark: #2a2a2a;
    --button-top: #efa80a;
    --button-bottom: #d77a04;
    --button-shadow: #7a3d00;
    --white: #ffffff;
  }
  * { box-sizing: border-box; margin: 0; padding: 0; }
  html, body {
    width: 1200px;
    height: 777px;
    overflow: hidden;
  }
  body {
    position: relative;
    font-family: "Montserrat", sans-serif;
    color: var(--white);
    background: var(--city-low);
  }
  .skyline-backdrop {
    position: absolute;
    inset: 0;
    background:
      radial-gradient(ellipse 420px 260px at 120px 300px, rgba(154,148,130,0.55), transparent 70%),
      radial-gradient(ellipse 380px 240px at 1120px 320px, rgba(120,124,118,0.45), transparent 70%),
      linear-gradient(180deg, var(--sky-top) 0%, var(--sky-mid) 38%, var(--sky-glow) 52%, var(--city-low) 78%, #1a1f22 100%);
  }
  .intro-frame {
    position: absolute;
    left: 0;
    top: 0;
    width: 1200px;
    height: 777px;
  }
  .brand-name {
    position: absolute;
    left: 486px;
    width: 228px;
    top: 140px;
    display: flex;
    align-items: center;
    justify-content: center;
    gap: 8px;
    font-weight: 600;
    font-size: 14px;
    letter-spacing: 0.5px;
    color: var(--gold-light);
  }
  .brand-dot {
    width: 10px;
    height: 10px;
    border-radius: 50%;
    background: var(--gold-light);
  }
  .intro-video {
    position: absolute;
    left: 211px;
    top: 219px;
    width: 778px;
    height: 383px;
    background: var(--white);
    padding: 6px;
  }
  .video-still {
    position: relative;
    width: 100%;
    height: 100%;
    background:
      linear-gradient(90deg, var(--photo-light) 0%, var(--photo-light) 45%, var(--photo-mid) 62%, var(--photo-dark) 80%, var(--photo-mid) 100%);
  }
  .play-button {
    position: absolute;
    left: 50%;
    top: 50%;
    width: 130px;
    height: 130px;
    transform: translate(-50%, -50%);
  }
  .enter-button {
    position: absolute;
    left: 457px;
    top: 623px;
    width: 286px;
    height: 62px;
    display: flex;
    align-items: center;
    justify-content: center;
    border-radius: 3px;
    background: linear-gradient(180deg, var(--button-top), var(--button-bottom));
    box-shadow: 0 4px 0 var(--button-shadow);
    font-weight: 700;
    font-size: 21px;
    color: var(--white);
    text-decoration: none;
  }
  .site-footer {
    position: absolute;
    left: 0;
    right: 0;
    top: 738px;
    text-align: center;
    font-size: 16px;
    font-weight: 400;
    color: var(--white);
  }
</style>
</head>
<body>
  <div class="skyline-backdrop" role="img" aria-label="Blurred night skyline of West Bay, Doha"></div>

  <svg class="intro-frame" viewBox="0 0 1200 777" aria-hidden="true">
    <defs>
      <linearGradient id="panelFill" x1="0" y1="0" x2="0" y2="1">
        <stop offset="0" stop-color="var(--panel-top)"/>
        <stop offset="0.35" stop-color="#120904"/>
        <stop offset="1" stop-color="var(--panel-bottom)"/>
      </linearGradient>
    </defs>
    <path d="M155 133 H486 C530 122 560 62 600 26 C640 62 670 122 714 133 H1045 V713 H155 Z"
          fill="url(#panelFill)" stroke="var(--gold)" stroke-width="3" stroke-linejoin="round"/>
  </svg>

  <div class="brand-name"><span class="brand-dot"></span>Lumara Maid Service</div>

  <div class="intro-video">
    <div class="video-still" role="img" aria-label="Maid in uniform making a hotel bed"></div>
    <svg class="play-button" viewBox="0 0 130 130" aria-label="Play intro video" role="img">
      <circle cx="65" cy="65" r="61" fill="none" stroke="var(--white)" stroke-width="7"/>
      <path d="M46 32 L100 65 L46 98 Z" fill="var(--white)"/>
    </svg>
  </div>

  <a class="enter-button" href="#">Enter The Site</a>

  <footer class="site-footer">© 2014 Copyrights Reserved</footer>
</body>
</html>
```